IT Support Business needs a Flyer Designed

Have just had new logo and business cards made for new business called Byte Harbor, am now in need of a new flyer design. Byte Harbor will be providing home and small business it support.
Updates
Byte Harbor flyer design brief has been uploaded. The contest has also been changed to payment guaranteed.
If you need anymore information please feel free to contact myself.
Project Deadline Extended
Reason: I signed up early to take advantage of the artfolly 24 hour sale, and was a few days late in providing a design brief. Therefore I am extending the deadline by 2 days, to ensure it lasts for a good 2 weeks.
Have worked on and refined the Design Brief a bit more, hoping it makes it a bit clearer as to what I want on the flyer. If you have any questions please do not hesitate to ask.
I have refined the design brief overnight, after receiving some feedback, please refer to newly uploaded file for this morning. I am hoping it makes things clearer and easier.
Industry/Entity Type
Small Business

```html
<!DOCTYPE html>
<html lang="en">
<head>
<meta charset="utf-8">
<title>Byte Harbor – Computer Repair Flyer</title>
<link rel="stylesheet" href="https://fonts.googleapis.com/css2?family=Bitter:wght@400&family=Oxygen:wght@400;700&display=swap">
<style>
  :root {
    --paper: #ffffff;
    --ink: #2b2b2b;
    --icon: #444547;
    --label: #3a3a3a;
    --brand-blue: #1f6fb5;
    --deep-blue: #1c5e9c;
    --accent-red: #e4322b;
    --rule: #d9d9d9;
    --photo-dark: #3a4f86;
    --photo-mid: #7d8fbd;
    --photo-light: #dfe5f2;
  }
  * { margin: 0; padding: 0; box-sizing: border-box; }
  html, body { width: 1200px; height: 798px; overflow: hidden; background: var(--paper); }
  .flyer { position: relative; width: 1200px; height: 798px; background: var(--paper); overflow: hidden; font-family: "Oxygen", Arial, sans-serif; }
  .swooshes { position: absolute; inset: 0; width: 1200px; height: 798px; }
  .hero-photo {
    position: absolute; left: 39px; top: 43px; width: 1119px; height: 249px;
    background: radial-gradient(ellipse at 35% 40%, var(--photo-light) 0%, var(--photo-mid) 35%, var(--photo-dark) 75%),
                var(--photo-dark);
  }
  .logo-tab {
    position: absolute; left: 698px; top: 0; width: 502px; height: 137px;
    background: var(--paper); border-bottom-left-radius: 60px;
    display: flex; align-items: center; justify-content: center; gap: 14px;
  }
  .logo-dot { width: 30px; height: 30px; border-radius: 50%; background: var(--accent-red); }
  .logo-name { font-family: "Oxygen", Arial, sans-serif; font-weight: 700; font-size: 46px; color: var(--brand-blue); letter-spacing: 1px; }
  .headline {
    position: absolute; left: 0; right: 0; top: 318px; text-align: center;
    font-family: "Bitter", Georgia, serif; font-weight: 400; font-size: 61px; line-height: 72px; color: var(--ink);
  }
  .services { position: absolute; left: 29px; top: 443px; width: 1160px; display: grid; grid-template-columns: repeat(8, 1fr); list-style: none; }
  .service { display: flex; flex-direction: column; align-items: center; text-align: center; }
  .service svg { width: 66px; height: 66px; fill: var(--icon); }
  .service-label { margin-top: 20px; font-size: 16px; line-height: 20px; color: var(--label); }
  .pricing {
    position: absolute; left: 80px; right: 80px; top: 641px; border-top: 1px solid var(--rule);
    padding-top: 10px; text-align: center; color: var(--accent-red); font-size: 23px; line-height: 34px;
  }
</style>
</head>
<body>
<main class="flyer">
  <div class="hero-photo" role="img" aria-label="Photo of a stethoscope resting on a laptop keyboard in blue tones"></div>

  <svg class="swooshes" viewBox="0 0 1200 798" aria-hidden="true">
    <path d="M0 0 H300 C180 20 60 70 0 150 Z" fill="var(--accent-red)"/>
    <path d="M0 55 C70 25 170 12 270 10 C150 30 60 80 0 160 Z" fill="var(--paper)"/>
    <path d="M0 75 C60 45 140 30 230 24 C130 50 50 100 0 170 Z" fill="var(--deep-blue)"/>
    <path d="M0 100 C50 70 120 52 200 42 C110 70 40 120 0 190 Z" fill="var(--paper)"/>
    <path d="M1200 560 C1160 680 1060 760 900 798 H1200 Z" fill="var(--deep-blue)"/>
    <path d="M1200 585 C1150 690 1050 765 930 798 H960 C1080 768 1170 700 1200 610 Z" fill="var(--accent-red)"/>
    <path d="M1200 560 C1175 650 1110 720 1010 768 C1100 735 1170 670 1200 600 Z" fill="var(--accent-red)"/>
  </svg>

  <div class="logo-tab">
    <span class="logo-dot"></span>
    <span class="logo-name">Byte Harbor</span>
  </div>

  <h1 class="headline">Computer Repair You Can Depend On</h1>

  <ul class="services">
    <li class="service">
      <svg viewBox="0 0 72 72"><rect x="10" y="12" width="48" height="34" rx="3" fill="none" stroke="var(--icon)" stroke-width="4"/><rect x="4" y="48" width="60" height="6" rx="2"/><path d="M30 36 L48 18 L54 22 L36 40 Z"/></svg>
      <span class="service-label">Computer<br>Repair, Service,<br>Install And<br>Upgrade</span>
    </li>
    <li class="service">
      <svg viewBox="0 0 72 72"><rect x="24" y="6" width="24" height="16" rx="2"/><path d="M34 22 H38 V32 H58 V44 H54 V36 H38 V44 H34 V36 H18 V44 H14 V32 H34 Z"/><circle cx="16" cy="54" r="9"/><circle cx="36" cy="54" r="9"/><circle cx="56" cy="54" r="9"/></svg>
      <span class="service-label">Setting Up<br>Secure<br>Networks</span>
    </li>
    <li class="service">
      <svg viewBox="0 0 72 72"><rect x="12" y="8" width="46" height="52" rx="5" fill="none" stroke="var(--icon)" stroke-width="4"/><rect x="20" y="16" width="30" height="34" fill="none" stroke="var(--icon)" stroke-width="2"/><path d="M34 30 V56 L28 50 L26 52 L36 66 H50 L52 44 L40 40 V30 Z"/></svg>
      <span class="service-label">Setting up<br>New<br>Hardware</span>
    </li>
    <li class="service">
      <svg viewBox="0 0 72 72"><rect x="2" y="14" width="8" height="8"/><rect x="12" y="14" width="8" height="8"/><rect x="22" y="14" width="8" height="8"/><rect x="32" y="14" width="8" height="8"/><rect x="42" y="14" width="8" height="8"/><rect x="52" y="14" width="8" height="8"/><rect x="62" y="14" width="8" height="8"/><path d="M40 28 L40 58 L47 51 L52 62 L57 60 L52 49 L62 49 Z"/></svg>
      <span class="service-label">Software<br>Install And<br>Configuration</span>
    </li>
    <li class="service">
      <svg viewBox="0 0 72 72"><path d="M36 18 C24 18 18 27 18 35 C18 43 26 47 27 54 H45 C46 47 54 43 54 35 C54 27 48 18 36 18 Z"/><rect x="28" y="57" width="16" height="4"/><rect x="30" y="63" width="12" height="4"/><path d="M34 2 H38 V12 H34 Z M10 14 L13 11 L20 18 L17 21 Z M62 14 L59 11 L52 18 L55 21 Z M2 34 H12 V38 H2 Z M60 34 H70 V38 H60 Z"/></svg>
      <span class="service-label">Software<br>Tricks, Tips<br>and Tutorials</span>
    </li>
    <li class="service">
      <svg viewBox="0 0 72 72"><rect x="4" y="8" width="40" height="28" fill="none" stroke="var(--icon)" stroke-width="4"/><path d="M4 8 L24 26 L44 8" fill="none" stroke="var(--icon)" stroke-width="4"/><circle cx="44" cy="46" r="16" fill="none" stroke="var(--icon)" stroke-width="5"/><circle cx="44" cy="46" r="6" fill="none" stroke="var(--icon)" stroke-width="4"/><path d="M50 40 V52 C50 56 58 56 60 50" fill="none" stroke="var(--icon)" stroke-width="4"/></svg>
      <span class="service-label">Internet<br>and Email<br>Setup</span>
    </li>
    <li class="service">
      <svg viewBox="0 0 72 72"><path d="M18 50 C8 50 4 42 8 36 C6 28 14 22 22 26 C26 14 46 12 52 24 C62 22 70 32 64 42 C66 48 60 50 56 50 Z" fill="none" stroke="var(--icon)" stroke-width="4"/><path d="M24 34 L34 26 V31 H46 V37 H34 V42 Z"/><path d="M56 48 L46 56 V51 H34 V45 H46 V40 Z"/></svg>
      <span class="service-label">Data Backup<br>and Recovery</span>
    </li>
    <li class="service">
      <svg viewBox="0 0 72 72"><circle cx="36" cy="26" r="14"/><path d="M18 26 C18 10 54 10 54 26" fill="none" stroke="var(--icon)" stroke-width="4"/><rect x="14" y="22" width="7" height="12" rx="2"/><rect x="51" y="22" width="7" height="12" rx="2"/><path d="M54 34 C54 40 48 42 40 42" fill="none" stroke="var(--icon)" stroke-width="3"/><path d="M12 68 C12 52 24 46 36 46 C48 46 60 52 60 68 Z"/></svg>
      <span class="service-label">Onsite and<br>Remote<br>Support<br>Available</span>
    </li>
  </ul>

  <section class="pricing">
    <p>$40 Per Hour Specific Job, Or Am Happy To Bundle, Provide Flexible Pricing For More Complex Tasks</p>
    <p>No Call Out Fee</p>
    <p>Friendly, Hassle Free, Independent Advice And Recommendations Given</p>
  </section>
</main>
</body>
</html>
```